Granite Bureau of Analysis Card Design

I need a business card for the agency I currently am tasked with, which is based in Hartford, CT. GBAN provides, disseminates and obtains intelligence in regards to ongoing criminal investigations throughout the State of CT. The information we obtain and provide, comes to us and is sent out by various Law Enforcement agencies throughout CT.

Industry/Entity Type

Business

Contact Information for Business Card

Officer Lyle P. Harrowby
Bramford Police Department - Eastern Region Intelligence Officer
Granite Bureau of Analysis
4827 Willowmere Ave., Middletown, CT 06457
Work Cell: (555) 318-2694
E-Mail: gban.wd@gbanmail.example

```html
<!DOCTYPE html>
<html lang="en">
<head>
<meta charset="utf-8">
<title>Granite Bureau of Analysis — Business Card</title>
<link href="https://fonts.googleapis.com/css2?family=Oswald:wght@400;500;600&display=swap" rel="stylesheet">
<style>
  :root {
    --page-bg: #e9e6e1;
    --card-white: #f7f7f7;
    --card-grey: #e2e2e2;
    --edge-yellow: #f3e034;
    --band-red: #c8192c;
    --ink: #1c1c1c;
    --ink-soft: #3a3a3a;
    --on-red: #ffffff;
  }
  * { box-sizing: border-box; margin: 0; padding: 0; }
  html, body {
    width: 1200px; height: 970px; overflow: hidden;
    background: var(--page-bg);
    font-family: "Oswald", "Arial Narrow", sans-serif;
  }
  .canvas { position: relative; width: 1200px; height: 970px; }
  .card {
    position: absolute; left: 250px;
    width: 700px; height: 400px;
    background: linear-gradient(135deg, var(--card-white) 0%, var(--card-grey) 100%);
    border-left: 8px solid var(--edge-yellow);
    border-bottom: 8px solid var(--edge-yellow);
    box-shadow: 0 10px 24px rgba(0,0,0,0.18);
    overflow: hidden;
  }
  .card--back { top: 50px; }
  .card--front { top: 510px; }

  .agency-mark {
    display: flex; align-items: center; gap: 10px;
    color: var(--ink); font-weight: 600;
    text-transform: uppercase; letter-spacing: 1px;
    white-space: nowrap;
  }
  .agency-mark__dot {
    width: 22px; height: 22px; border-radius: 50%;
    background: var(--ink); flex: none;
  }
  .card--back .agency-mark {
    position: absolute; left: 50%; top: 50%;
    transform: translate(-50%, -50%);
    font-size: 30px;
  }
  .card--front .agency-mark {
    position: absolute; left: 60px; top: 48px;
    font-size: 24px;
  }
  .red-band {
    position: absolute; left: 0; right: 0; top: 150px; height: 190px;
    background: var(--band-red);
    color: var(--on-red);
    padding: 18px 60px;
  }
  .person-name {
    font-size: 34px; font-weight: 600; letter-spacing: 1px; line-height: 1.1;
    text-transform: uppercase;
  }
  .person-title {
    font-size: 14px; font-weight: 400; letter-spacing: 2px;
    text-transform: uppercase; margin-bottom: 16px;
  }
  .contact-grid {
    display: grid; grid-template-columns: 190px 1fr; row-gap: 12px;
    font-size: 14px; font-weight: 400; letter-spacing: 0.5px;
  }
  .contact-item { display: flex; align-items: center; gap: 8px; white-space: nowrap; }
  .contact-item svg { width: 20px; height: 20px; flex: none; }
  .street-address {
    position: absolute; left: 60px; bottom: 14px;
    font-size: 17px; color: var(--ink-soft); letter-spacing: 1px;
    white-space: nowrap;
  }
</style>
</head>
<body>
<main class="canvas">

  <section class="card card--back" aria-label="Card back">
    <div class="agency-mark">
      <span class="agency-mark__dot"></span>
      <span>Bramford Police</span>
    </div>
  </section>

  <section class="card card--front" aria-label="Card front">
    <div class="agency-mark">
      <span class="agency-mark__dot"></span>
      <span>Bramford Police</span>
    </div>

    <div class="red-band">
      <h1 class="person-name">Marcus Ellery</h1>
      <p class="person-title">General Manager</p>
      <div class="contact-grid">
        <div class="contact-item">
          <svg viewBox="0 0 20 20" aria-hidden="true"><circle cx="10" cy="10" r="9" fill="none" stroke="#fff" stroke-width="1.3"/><path d="M7 5.5l1.6 2-1 1.2c.7 1.5 1.7 2.5 3.2 3.2l1.2-1 2 1.6-1 1.5c-3.5-.3-6.7-3.5-7-7z" fill="#fff"/></svg>
          <span>555 204 7716</span>
        </div>
        <div class="contact-item">
          <svg viewBox="0 0 20 20" aria-hidden="true"><circle cx="10" cy="10" r="9" fill="none" stroke="#fff" stroke-width="1.3"/><rect x="5.5" y="7" width="9" height="6.5" fill="none" stroke="#fff" stroke-width="1.2"/><path d="M5.5 7l4.5 3.5L14.5 7" fill="none" stroke="#fff" stroke-width="1.2"/></svg>
          <span>yourname@mail.example</span>
        </div>
        <div class="contact-item">
          <svg viewBox="0 0 20 20" aria-hidden="true"><circle cx="10" cy="10" r="9" fill="none" stroke="#fff" stroke-width="1.3"/><rect x="7" y="5" width="6" height="10" rx="1" fill="none" stroke="#fff" stroke-width="1.2"/><circle cx="10" cy="13" r=".8" fill="#fff"/></svg>
          <span>555 204 7738</span>
        </div>
        <div class="contact-item">
          <svg viewBox="0 0 20 20" aria-hidden="true"><circle cx="10" cy="10" r="9" fill="none" stroke="#fff" stroke-width="1.3"/><circle cx="10" cy="10" r="5" fill="none" stroke="#fff" stroke-width="1.1"/><path d="M5 10h10M10 5c-2 2.8-2 7.2 0 10M10 5c2 2.8 2 7.2 0 10" fill="none" stroke="#fff" stroke-width="1"/></svg>
          <span>www.yoursite.example</span>
        </div>
      </div>
    </div>

    <p class="street-address">214 Harbor Lane, 2nd Floor Suite, W.</p>
  </section>

</main>
</body>
</html>
```